Aunt Roula's Bakery

I am about to create a luxury boutique that specializes in cake baking and cupcake
and ready for parties and special events and order delivery
the logo has already made

Boutique

Email:auntroulasbakery@mailbox-example.net
Instagram: aunt_roula_bakery
Twitter: xxxxxxx
WhatsApp: xxxxxxx

Requirements
Must have
• luxury design

```html
<!DOCTYPE html>
<html lang="en">
<head>
<meta charset="utf-8">
<title>Aunt Roula's Bakery – Business Cards</title>
<link href="https://fonts.googleapis.com/css2?family=PT+Sans:wght@400;700&display=swap" rel="stylesheet">
<style>
  :root {
    --backdrop: #3b3b3b;
    --card: #f7f7f7;
    --rose: #d4899b;
    --rose-soft: #e8bcc6;
    --stone: #7b7773;
    --ink: #4f4c4a;
  }
  * { margin: 0; padding: 0; box-sizing: border-box; }
  html, body {
    width: 1200px; height: 750px; overflow: hidden;
    background: var(--backdrop);
    font-family: "PT Sans", sans-serif;
  }
  .canvas { position: relative; width: 1200px; height: 750px; }
  .card {
    position: absolute; top: 228px;
    width: 461px; height: 263px;
    background: var(--card);
  }
  .card--front { left: 124px; }
  .card--back { left: 618px; }
  .centered {
    position: absolute; left: 50%;
    transform: translate(-50%, -50%);
    white-space: nowrap; line-height: 1;
  }
  .emblem {
    position: absolute; left: 50%; transform: translate(-50%, -50%);
    border-radius: 50%; background: var(--rose);
    border: 3px solid #fff; box-shadow: 0 0 0 2px var(--stone);
  }
  .wordmark { color: var(--stone); font-weight: 400; text-transform: uppercase; }
  .wordmark--name { letter-spacing: 0.5px; }
  .wordmark--trade { letter-spacing: 12px; padding-left: 12px; }
  .rule { position: absolute; height: 2px; background: var(--rose); }
  .flourish {
    position: absolute;
    background: linear-gradient(90deg, transparent, var(--rose-soft) 20%, #c9c5c2 50%, var(--rose-soft) 80%, transparent);
    border-radius: 40%;
    opacity: 0.7;
  }
  .person-name { color: var(--rose); font-size: 17px; font-weight: 700; }
  .person-role { color: var(--stone); font-size: 13px; }
  .contact {
    color: var(--ink); font-size: 11.5px;
    display: flex; align-items: center; gap: 4px;
  }
  .contact-group { display: inline-flex; align-items: center; gap: 4px; margin: 0 5px; }
  .contact svg { width: 11px; height: 11px; fill: var(--rose); flex: none; }
  .dot { width: 9px; height: 9px; border-radius: 50%; border: 1.5px solid var(--rose); flex: none; }
  .web { color: var(--ink); font-size: 12px; letter-spacing: 1px; }
</style>
</head>
<body>
<main class="canvas">

  <section class="card card--front" aria-label="Front of card">
    <div class="emblem" style="top:34px;width:50px;height:50px;"></div>
    <div class="centered wordmark wordmark--name" style="top:84px;font-size:28px;">Aunt Roula's</div>
    <div class="rule" style="top:97px;left:120px;width:222px;"></div>
    <div class="centered wordmark wordmark--trade" style="top:111px;font-size:15px;">Bakery</div>

    <div class="centered person-name" style="top:134px;">Nadia Karam</div>
    <div class="centered person-role" style="top:151px;">CEO/Founder</div>

    <div class="centered contact" style="top:170px;">
      <span class="contact-group">
        <svg viewBox="0 0 24 24"><path d="M6.6 10.8a15.2 15.2 0 0 0 6.6 6.6l2.2-2.2a1 1 0 0 1 1-.25 11.4 11.4 0 0 0 3.6.57 1 1 0 0 1 1 1V20a1 1 0 0 1-1 1A17 17 0 0 1 3 4a1 1 0 0 1 1-1h3.5a1 1 0 0 1 1 1c0 1.25.2 2.45.57 3.57a1 1 0 0 1-.25 1z"/></svg>
        555 014 2738
      </span>
      <span class="contact-group">
        <svg viewBox="0 0 24 24"><path d="M2 5h20v14H2z M2 5l10 8 10-8" fill="none" stroke="#d4899b" stroke-width="2.4"/></svg>
        auntroulasbakery@mailbox-example.net
      </span>
    </div>
    <div class="centered contact" style="top:188px;">
      <span class="contact-group"><span class="dot"></span>aunt_roula_bakery</span>
      <span class="contact-group"><span class="dot"></span>auntroulasbakery</span>
    </div>
    <div class="centered contact" style="top:206px;">
      <span class="contact-group"><span class="dot"></span>auntroulasbakery</span>
    </div>

    <div class="rule" style="top:219px;left:176px;width:110px;"></div>
    <div class="flourish" role="img" aria-label="Decorative scroll flourish" style="top:225px;left:182px;width:96px;height:30px;"></div>
  </section>

  <section class="card card--back" aria-label="Back of card">
    <div class="emblem" style="top:84px;width:54px;height:54px;"></div>
    <div class="rule" style="top:117px;left:128px;width:200px;"></div>
    <div class="centered wordmark wordmark--name" style="top:135px;font-size:27px;">Aunt Roula's</div>
    <div class="rule" style="top:148px;left:128px;width:200px;"></div>
    <div class="centered wordmark wordmark--trade" style="top:161px;font-size:15px;">Bakery</div>
    <div class="rule" style="top:170px;left:166px;width:122px;"></div>
    <div class="flourish" role="img" aria-label="Decorative scroll flourish" style="top:176px;left:174px;width:108px;height:34px;"></div>
    <div class="centered web" style="top:234px;">www.auntroulas-example.com</div>
  </section>

</main>
</body>
</html>
```